Company or website name
- dalewintham.com
- Links to the website
- Vita Forge
- Describe your company and organization and target audience
- Founded by celebrity personal trainer and media personality Dale Wintham, Vita Forge provides high quality on-site fitness and wellness classes, and personal trainers for businesses and residential gyms throughout New York City. Our target audience are residents of high end buildings in NYC, that expect excellence and luxury
- The design should have the following
- This is a 24"x36" Poster for a complimentary event at a high end building. I would like the poster to look high end, luxury and simple and chique. The words should be clear and easy to read. It would be great to have a final copy that we can send to the printer and one which we can edit for future events Here is the text: The Halcott Spires Gym Complimentary Fitness & Wellness Event Complimentary Yoga, Pilates & Interval Training Bootcamp Classes PLUS: 30 Minute Private Training Sessions *Kids Karate Classes Also Available Saturday May 18th, 25th & June 1st Time: 9:00am - 12:15pm Halcott Spires Gym Schedule: 9:00am - 9:30am Yoga 9:45am - 10:15am Interval Training Bootcamp 11:45am -12:15pm Pilates 9:00am - 12:00pm Private Training Sessions Special Introductory Rate on Future Packages During Promotion www.Vitaforge.tv Info@vitaforge.tv
- Other Facts

```html
<!DOCTYPE html>
<html lang="en">
<head>
<meta charset="utf-8">
<title>The Halcott Spires Gym – Complimentary Fitness &amp; Wellness</title>
<link rel="stylesheet" href="https://fonts.googleapis.com/css2?family=Oswald:wght@500;600;700&family=Roboto:wght@400;700&display=swap">
<style>
  :root {
    --page: #ffffff;
    --poster-black: #050505;
    --white: #ffffff;
    --sky-blue: #1a8fdc;
    --band-blue-light: #2196e6;
    --band-blue-dark: #2a3fae;
    --lime: #9fd03e;
    --olive: #5e7f2a;
    --skin-light: #c99a78;
    --skin-dark: #2b1f19;
  }
  * { margin: 0; padding: 0; box-sizing: border-box; }
  html, body {
    width: 1200px;
    height: 960px;
    overflow: hidden;
    background: var(--page);
  }
  .poster {
    position: absolute;
    left: 300px;
    top: 31px;
    width: 600px;
    height: 895px;
    background: var(--poster-black);
    overflow: hidden;
    color: var(--white);
  }
  .poster-title {
    position: absolute;
    top: 16px;
    left: 0;
    width: 100%;
    text-align: center;
    font-family: "Oswald", sans-serif;
    font-weight: 700;
    font-size: 50px;
    line-height: 60px;
    text-transform: uppercase;
    white-space: nowrap;
  }
  .poster-subtitle {
    position: absolute;
    top: 78px;
    left: 0;
    width: 100%;
    text-align: center;
    font-family: "Oswald", sans-serif;
    font-weight: 700;
    font-size: 35px;
    line-height: 44px;
    color: var(--sky-blue);
    text-transform: uppercase;
    white-space: nowrap;
  }
  .contact-line {
    position: absolute;
    left: 14px;
    top: 124px;
    height: 360px;
    writing-mode: vertical-rl;
    transform: rotate(180deg);
    font-family: "Roboto", sans-serif;
    font-size: 19px;
    color: var(--lime);
    white-space: nowrap;
    text-align: left;
    z-index: 3;
  }
  .athlete-photo {
    position: absolute;
    left: 30px;
    top: 140px;
    width: 230px;
    height: 720px;
    background: radial-gradient(ellipse at 50% 35%, var(--skin-light) 0%, rgba(120, 85, 65, 0.7) 35%, rgba(43, 31, 25, 0.25) 70%, transparent 100%);
    z-index: 2;
  }
  .offer-band {
    position: absolute;
    left: 189px;
    top: 153px;
    width: 411px;
    height: 108px;
    background: linear-gradient(90deg, var(--band-blue-light), var(--band-blue-dark));
    padding: 4px 14px 0 0;
    text-align right;
    text-align: right;
    font-family: "Oswald", sans-serif;
    font-weight: 600;
    font-size: 27px;
    line-height: 33px;
    text-transform: uppercase;
    white-space: nowrap;
    z-index: 1;
  }
  .private-sessions {
    position: absolute;
    left: 232px;
    top: 278px;
    font-family: "Oswald", sans-serif;
    font-weight: 600;
    font-size: 55px;
    line-height: 64px;
    white-space: nowrap;
    z-index: 3;
  }
  .schedule-band {
    position: absolute;
    left: 0;
    top: 480px;
    width: 600px;
    height: 194px;
    background: var(--olive);
    z-index: 1;
  }
  .schedule {
    position: absolute;
    right: 14px;
    top: 505px;
    text-align: right;
    white-space: nowrap;
    z-index: 3;
  }
  .schedule-heading {
    font-family: "Oswald", sans-serif;
    font-weight: 500;
    font-size: 30px;
    line-height: 38px;
    text-transform: uppercase;
  }
  .schedule-list {
    list-style: none;
    font-family: "Roboto", sans-serif;
    font-size: 16px;
    line-height: 23px;
  }
  .schedule-list .session-name { font-weight: 700; }
  .schedule-list .session-name::before { content: "•"; margin-right: 2px; }
  .schedule-dates {
    font-family: "Roboto", sans-serif;
    font-size: 16px;
    line-height: 23px;
  }
  .brand-mark {
    position: absolute;
    right: 14px;
    bottom: 60px;
    display: flex;
    align-items: center;
    gap: 14px;
    z-index: 3;
  }
  .brand-name {
    font-family: "Oswald", sans-serif;
    font-weight: 500;
    font-size: 44px;
    line-height: 52px;
    color: var(--white);
    text-transform: uppercase;
    white-space: nowrap;
  }
</style>
</head>
<body>
  <main class="poster">
    <h1 class="poster-title">The Halcott Spires Gym</h1>
    <h2 class="poster-subtitle">Complimentary Fitness &amp; Wellness</h2>

    <p class="contact-line">www.Vitaforge.tv Info@vitaforge.tv</p>

    <div class="athlete-photo" role="img" aria-label="Photo of a fit woman in black sportswear throwing a punch while lifting one knee"></div>

    <p class="offer-band">Complimentary Yoga,<br>Pilates &amp; Interval Training<br>Bootcamp Classes</p>

    <p class="private-sessions">PLUS: 30 Minute<br>Private Training<br>Sessions</p>

    <div class="schedule-band"></div>
    <section class="schedule">
      <h3 class="schedule-heading">Schedule:</h3>
      <ul class="schedule-list">
        <li><span class="session-name">Halcott Spires Gym</span> 9:00am - 9:30am</li>
        <li><span class="session-name">Yoga</span> 9:45am - 10:15am</li>
        <li><span class="session-name">Interval Training Bootcamp</span> 11:45am -12:15pm</li>
        <li><span class="session-name">Pilates</span> 9:00am - 12:00pm</li>
        <li><span class="session-name">Kids Karate Classes Also Available</span></li>
      </ul>
      <p class="schedule-dates">Saturday May 18th, 25th &amp; June 1st Time: 9:00am - 12:15pm</p>
    </section>

    <div class="brand-mark">
      <svg width="40" height="40" viewBox="0 0 40 40" aria-hidden="true">
        <circle cx="20" cy="20" r="17" fill="none" stroke="#ffffff" stroke-width="4"/>
      </svg>
      <span class="brand-name">Vita Forge</span>
    </div>
  </main>
</body>
</html>
```